Business card for medical clinic

I need an upmarket, modern medical/health business card for my clinic

Contact Information for Business Card

name, address, email, qr code

```html
<!DOCTYPE html>
<html lang="en">
<head>
<meta charset="utf-8">
<title>Meridian Care Clinic – Business Card</title>
<link href="https://fonts.googleapis.com/css2?family=Montserrat:wght@400;500;700&display=swap" rel="stylesheet">
<style>
  :root {
    --backdrop: #c9c9cb;
    --paper: #ffffff;
    --navy: #1f2a48;
    --blue: #2ba3dc;
    --mid-blue: #2f6f96;
    --ink: #1b1b1b;
  }
  * { box-sizing: border-box; margin: 0; padding: 0; }
  html, body { width: 1200px; height: 813px; overflow: hidden; }
  body {
    background: var(--backdrop);
    font-family: "Montserrat", Arial, sans-serif;
    position: relative;
  }
  .card {
    position: absolute;
    top: 246px;
    width: 540px;
    height: 320px;
    border-radius: 22px;
    overflow: hidden;
    box-shadow: 0 14px 30px rgba(0,0,0,0.28);
  }
  .card--front { left: 40px; background: var(--paper); }
  .card--back {
    left: 620px;
    background: linear-gradient(70deg, var(--blue) 0%, var(--mid-blue) 40%, var(--navy) 100%);
    color: #fff;
  }
  .front-bands { position: absolute; inset: 0; width: 100%; height: 100%; }
  .brand {
    position: absolute;
    font-weight: 700;
    text-transform: uppercase;
    letter-spacing: 0.08em;
    line-height: 1.15;
  }
  .card--front .brand {
    left: 34px; top: 40px;
    color: var(--navy);
    font-size: 19px;
    display: flex; align-items: center; gap: 12px;
  }
  .brand-dot {
    width: 30px; height: 30px; border-radius: 50%;
    background: var(--blue); flex: none;
  }
  .holder {
    position: absolute; right: 44px; top: 36px; text-align: right;
  }
  .holder-name {
    color: var(--blue); font-weight: 700; font-size: 22px; letter-spacing: 0.01em;
  }
  .holder-role { color: var(--ink); font-size: 14px; font-weight: 500; margin-top: 2px; }
  .name-tab {
    position: absolute; right: 0; top: 30px; width: 16px; height: 30px; background: var(--blue);
  }
  .address {
    position: absolute; left: 34px; top: 152px;
    font-size: 14px; font-weight: 500; color: var(--ink); line-height: 1.35;
  }
  .contact-list {
    position: absolute; left: 34px; top: 210px; list-style: none;
    font-size: 14px; font-weight: 500; color: var(--ink);
  }
  .contact-list li { display: flex; align-items: center; gap: 10px; height: 23px; }
  .contact-list svg { width: 15px; height: 15px; flex: none; }
  .card--back .brand {
    left: 0; right: 0; top: 112px; text-align: center;
    font-size: 32px; font-weight: 500; letter-spacing: 0.12em;
  }
  .card--back .brand small {
    display: block; font-size: 17px; letter-spacing: 0.45em; margin-top: 6px; font-weight: 500;
  }
  .web {
    position: absolute; left: 0; right: 0; bottom: 36px;
    display: flex; justify-content: center; align-items: center; gap: 8px;
    font-size: 14px; letter-spacing: 0.03em;
  }
  .web svg { width: 16px; height: 16px; }
</style>
</head>
<body>

<section class="card card--front" aria-label="Business card front">
  <svg class="front-bands" viewBox="0 0 540 320" preserveAspectRatio="none" aria-hidden="true">
    <polygon points="230,320 250,298 540,150 540,320" fill="var(--navy)"/>
    <polygon points="250,298 262,282 540,132 540,150" fill="var(--blue)"/>
  </svg>
  <div class="name-tab"></div>
  <div class="brand"><span class="brand-dot"></span><span>Meridian Care<br>Clinic</span></div>
  <div class="holder">
    <div class="holder-name">DANA HOLLOWAY</div>
    <div class="holder-role">Managing Director</div>
  </div>
  <p class="address">482 Larkspur Ave, Ste<br>210, Fairview, TX 75069</p>
  <ul class="contact-list">
    <li>
      <svg viewBox="0 0 16 16"><path fill="var(--blue)" d="M3 1.5l3 .5 1 3.5-2 1.3a9 9 0 0 0 4.2 4.2l1.3-2 3.5 1 .5 3c-.2 1-1 1.5-2 1.5A13 13 0 0 1 1.5 3.5c0-1 .5-1.8 1.5-2z"/></svg>
      555-018-2740
    </li>
    <li>
      <svg viewBox="0 0 16 16"><rect x="1" y="3" width="14" height="10" rx="1" fill="var(--blue)"/><path d="M1.5 4l6.5 5 6.5-5" stroke="#fff" stroke-width="1.3" fill="none"/></svg>
      hello@meridiancare.com
    </li>
    <li>
      <svg viewBox="0 0 16 16"><circle cx="8" cy="8" r="7" fill="var(--blue)"/><path d="M1 8h14M8 1c-3 3.5-3 10.5 0 14M8 1c3 3.5 3 10.5 0 14" stroke="#fff" stroke-width="1" fill="none"/></svg>
      www.meridiancare.com
    </li>
  </ul>
</section>

<section class="card card--back" aria-label="Business card back">
  <div class="brand">Meridian Care<small>Clinic</small></div>
  <div class="web">
    <svg viewBox="0 0 16 16"><circle cx="8" cy="8" r="7" stroke="#fff" stroke-width="1.2" fill="none"/><path d="M1 8h14M8 1c-3 3.5-3 10.5 0 14M8 1c3 3.5 3 10.5 0 14" stroke="#fff" stroke-width="1" fill="none"/></svg>
    www.meridiancare.com
  </div>
</section>

</body>
</html>
```